Luxury modern loose tea company web design

I am a high-end modern luxury loose leaf tea business. I have a website domain that is hosted on Shopify. I’m looking for designers that have a modern flair and are able to create websites that would easily attract major YouTube and Instagram influencers as well as a modern millennial.

Luxury is at the fore front of the design scheme and branding and should be incorporated in ALL aspects of the website. As well if designers are able to implement any unique features to make the shopping experience more fun and memorable that is a major bonus. The main colors I work with are black, silver and gold, once again reinforcing the luxury feel.

My brand is called Sip of Lume

Target Market(s)

The Modern Millenial, 21-40 (bullseye 28). He or she is a young professional that has a disposable income in which they do like to indulge with. They balance their demanding work schedules well and they have a work hard/play hard mindset. This professional is more likely to order their daily coffee from Brewvant as opposed to Ned Kallory and their social media profiles are a big indicator as to their hobbies and lifestyles outside of their work environment. They enjoy shopping at stores like Vexa, Halcyne, UrbanLoom/UrbanGent and for special occasions are willing to splurge at stores like Marlowe's, Hall Verdine and… They live a pretty active lifestyle and are highly influenced by social media trending products

Colors

Designer to choose colors to be used in the design.

Requirements
Must have
• luxury feel
• unique customer experience

```html
<!DOCTYPE html>
<html lang="en">
<head>
<meta charset="utf-8">
<title>Sip of Lume — Loose Leaf Teas</title>
<link rel="stylesheet" href="https://fonts.googleapis.com/css2?family=Marcellus&family=Raleway:wght@400;500;600&display=swap">
<style>
:root{
  --ink:#151515;
  --ink-soft:#1f1f1f;
  --gold:#7b6848;
  --gold-deep:#5b4524;
  --gold-line:#a48d62;
  --cream:#f4efe6;
  --white:#ffffff;
  --muted:#cfc6b5;
  --text-dark:#3a3a3a;
}
*{box-sizing:border-box;margin:0;padding:0}
html,body{width:1200px;height:4444px;overflow:hidden}
body{background:var(--ink);font-family:"Raleway",sans-serif;color:var(--white);position:relative}
section,header,footer{position:relative;width:1200px;overflow:hidden}
.abs{position:absolute}
.serif{font-family:"Marcellus",serif}
.center{text-align:center;left:0;width:1200px}
.btn{position:absolute;display:flex;align-items:center;justify-content:center;font-size:11px;letter-spacing:1px;font-weight:600;text-transform:uppercase}
.btn-gold{background:var(--gold-deep);color:var(--white)}
.btn-white{background:var(--white);color:var(--text-dark)}
.section-title{font-family:"Marcellus",serif;font-size:38px;font-weight:400}

/* hero */
.hero{height:898px;background:linear-gradient(180deg,#1b1b1b 0%,#2a2622 45%,#141414 80%,#101010 100%)}
.hero-photo{position:absolute;left:400px;top:330px;width:400px;height:400px;background:radial-gradient(ellipse at 50% 55%,#3a3a3a 0%,#1d1d1d 45%,rgba(20,20,20,0) 72%)}
.hero-table{position:absolute;left:0;top:610px;width:1200px;height:120px;background:linear-gradient(180deg,rgba(60,44,30,.0),rgba(58,42,28,.55),rgba(20,16,12,0))}
.social{left:118px;top:38px;display:flex;gap:10px}
.social span{width:11px;height:11px;border-radius:50%;background:var(--muted)}
.brand{top:30px;font-size:28px;letter-spacing:1px;color:#bda77c}
.utility{right:124px;top:38px;display:flex;gap:12px}
.nav{top:104px;display:flex;justify-content:center;gap:38px;font-size:14px}
.hero-title{top:196px;font-size:76px;font-family:"Marcellus",serif}
.hero-sub{top:286px;font-size:15px}
.steps{top:726px;display:flex;justify-content:center;gap:0}
.step{width:300px;text-align:center;font-family:"Marcellus",serif;font-size:17px;line-height:1.3}
.step svg{display:block;margin:0 auto 18px}

/* varieties */
.varieties{height:566px;background:var(--gold)}
.product{position:absolute;top:177px;width:200px;text-align:center}
.product-art{width:200px;height:156px;background:radial-gradient(ellipse at 50% 80%,#6b6a3b 0%,#4a4630 40%,rgba(123,104,72,0) 70%)}
.product-art.dark{background:radial-gradient(ellipse at 50% 80%,#2c2016 0%,#3a2a1c 40%,rgba(123,104,72,0) 70%)}
.product-art .box{width:96px;height:74px;margin:0 auto;background:#1a1a1a}
.product h3{font-family:"Marcellus",serif;font-weight:400;font-size:18px;margin-top:54px}
.product p{font-size:11px;margin-top:4px;color:var(--muted)}

/* about */
.about{height:344px;background:linear-gradient(180deg,#1a1a1a,#121212)}
.about p{left:225px;width:750px;font-size:13.5px;line-height:1.45;text-align:center}

/* split panels */
.split{height:426px}
.panel{position:absolute;background:var(--gold);text-align:center}
.panel p{font-size:13.5px;line-height:1.45;margin:0 auto}
.photo{position:absolute}

/* blogs */
.blogs{height:809px;background:radial-gradient(ellipse at 30% 30%,#2b2b2b 0%,#161616 60%)}
.card{position:absolute;top:166px;width:306px;height:456px;background:var(--white);color:var(--text-dark)}
.card .img{height:228px}
.card h4{font-family:"Marcellus",serif;font-weight:400;font-size:17px;margin:28px 24px 10px}
.card .meta{font-size:10px;color:#777;margin:0 24px 18px;display:flex;gap:14px}
.card p{font-size:12.5px;line-height:1.45;margin:0 24px;color:#555}
.card .more{font-size:11px;margin:16px 24px 0;display:flex;align-items:center;gap:8px;letter-spacing:.5px}

/* testimonials */
.testimonials{height:444px;background:linear-gradient(90deg,#3a2e24 0%,#241d17 40%,#2c241c 60%,#3d2f22 100%)}

/* perks */
.perks{height:217px;background:#232323}
.perk{position:absolute;top:62px;width:316px;height:101px;background:var(--gold-deep);border:1px solid var(--gold-line);display:flex;align-items:center;justify-content:center;gap:16px}
.perk strong{display:block;font-family:"Marcellus",serif;font-weight:400;font-size:16px}
.perk span{font-size:11px}

/* footer */
.site-footer{height:266px;background:var(--gold)}
.col h5{font-family:"Marcellus",serif;font-weight:400;font-size:24px;margin-bottom:14px}
.col li{list-style:none;font-size:12.5px;line-height:26px}
.contact li{display:flex;gap:10px;align-items:center}
.copyright{height:65px;background:#141414}
.cards{right:124px;top:22px;display:flex;gap:6px}
.cards span{width:36px;height:22px;background:#e8e3d8;border-radius:2px}
</style>
</head>
<body>

<header class="hero">
  <div class="hero-photo" role="img" aria-label="Steaming dark tea cup on a wooden table"></div>
  <div class="hero-table" role="img" aria-label="Wooden table surface"></div>
  <div class="abs social"><span></span><span></span><span></span><span></span><span></span></div>
  <div class="abs center brand serif">Sip of Lume</div>
  <div class="abs utility">
    <svg width="14" height="14" viewBox="0 0 14 14"><circle cx="7" cy="4" r="3" fill="#cfc6b5"/><path d="M1 14c0-4 3-6 6-6s6 2 6 6z" fill="#cfc6b5"/></svg>
    <svg width="14" height="14" viewBox="0 0 14 14"><path d="M7 13L1.5 7A3.2 3.2 0 017 2.8 3.2 3.2 0 0112.5 7z" fill="#cfc6b5"/></svg>
    <svg width="16" height="14" viewBox="0 0 16 14"><path d="M0 1h3l2 8h8l2-6H5" fill="none" stroke="#cfc6b5" stroke-width="1.5"/><circle cx="6" cy="12" r="1.4" fill="#cfc6b5"/><circle cx="12" cy="12" r="1.4" fill="#cfc6b5"/></svg>
  </div>
  <nav class="abs center nav"><span>Home</span><span>About</span><span>Leaf teas ▾</span><span>Blogs</span><span>Contact</span></nav>
  <h1 class="abs center hero-title">Loose Leaf Teas</h1>
  <p class="abs center hero-sub">Lorem Ipsum is simply dummy text of the printing and typesetting industry.</p>
  <div class="btn btn-gold" style="left:515px;top:344px;width:175px;height:47px">Shop Now</div>
  <div class="abs center steps">
    <div class="step">
      <svg width="80" height="54" viewBox="0 0 80 54"><path d="M6 50Q40 0 74 50z" fill="#8f8370"/></svg>
      LOOSE LEAF TEA
    </div>
    <div class="step">
      <svg width="80" height="54" viewBox="0 0 80 54"><ellipse cx="56" cy="12" rx="10" ry="8" fill="#8f8370"/><path d="M49 18L18 50" stroke="#8f8370" stroke-width="4" stroke-linecap="round"/></svg>
      2.5 TO 3 TEASPOONS<br>(PER PERSON)
    </div>
    <div class="step">
      <svg width="80" height="54" viewBox="0 0 80 54"><path d="M26 2h28M26 52h28M30 2c0 16 20 18 20 25S30 36 30 52M50 2c0 16-20 18-20 25s20 9 20 25" fill="none" stroke="#8f8370" stroke-width="3"/></svg>
      BREW FOR 4-6 MINS
    </div>
  </div>
</header>

<section class="varieties">
  <h2 class="abs center section-title" style="top:38px">Varieties Loose Leaf Teas</h2>
  <div class="product" style="left:131px"><div class="product-art" role="img" aria-label="Tin of green tea with loose leaves"><div class="box"></div></div><h3>Green Tea</h3><p>$18</p></div>
  <div class="product" style="left:374px"><div class="product-art" role="img" aria-label="Tin of sencha with loose leaves"><div class="box"></div></div><h3>Sencha</h3><p>$18</p></div>
  <div class="product" style="left:620px"><div class="product-art dark" role="img" aria-label="Tin of assam tea with loose leaves"><div class="box"></div></div><h3>Assam Tea</h3><p>$18</p></div>
  <div class="product" style="left:863px"><div class="product-art dark" role="img" aria-label="Tin of earl grey tea with loose leaves"><div class="box"></div></div><h3>Earl Grey Tea</h3><p>$18</p></div>
  <div class="btn btn-gold" style="left:512px;top:474px;width:175px;height:44px">Browse More</div>
</section>

<section class="about">
  <h2 class="abs center section-title" style="top:38px">About us</h2>
  <p class="abs" style="top:138px">Lorem Ipsum is simply dummy text of the printing and typesetting industry. Lorem Ipsum has been the industry's standard dummy text ever since the 1500s, when an unknown printer took a galley of type and scrambled it to make a type specimen book.<br>It has survived not only five centuries, but also the leap into electronic typesetting, remaining essentially unchanged. It was popularised in the 1960s with the release of Typeline sheets containing Lorem Ipsum passages, and more recently with desktop publishing software like Quillset Layout including versions of Lorem Ipsum.</p>
  <svg class="abs" style="left:584px;top:278px" width="32" height="8" viewBox="0 0 32 8"><circle cx="4" cy="4" r="3.5" fill="#fff"/><circle cx="16" cy="4" r="3.5" fill="#fff"/><circle cx="28" cy="4" r="3.5" fill="#fff"/></svg>
</section>

<section class="split" style="height:426px">
  <div class="panel" style="left:0;top:0;width:735px;height:414px">
    <h2 class="section-title" style="margin-top:48px">New Arrivals</h2>
    <p style="width:560px;margin-top:60px">Lorem Ipsum is simply dummy text of the printing and typesetting industry. Lorem Ipsum has been the industry's standard dummy text ever since the 1500s, when an unknown printer took a galley of type and scrambled it to make a type specimen book.<br><br>It has survived not only five centuries, but also the leap into electronic typesetting, remaining essentially unchanged.</p>
    <div class="btn btn-gold" style="left:300px;top:322px;width:174px;height:46px">Shop Now</div>
  </div>
  <div class="photo" role="img" aria-label="Tea being poured from a white teapot into a white cup" style="left:755px;top:0;width:445px;height:414px;background:linear-gradient(135deg,#e9e7e3 0%,#f7f6f3 45%,#d9c98c 70%,#ecebe7 100%)"></div>
</section>

<section class="split" style="height:409px">
  <div class="photo" role="img" aria-label="Clay teapot with loose tea leaves being added by hand" style="left:0;top:0;width:430px;height:409px;background:linear-gradient(135deg,#8a4f35 0%,#4a2a22 45%,#2a1f22 75%,#6d5a66 100%)"></div>
  <div class="panel" style="left:450px;top:0;width:750px;height:409px">
    <h2 class="section-title" style="margin-top:40px">Get % Discount</h2>
    <p style="width:570px;margin-top:60px">Lorem Ipsum is simply dummy text of the printing and typesetting industry. Lorem Ipsum has been the industry's standard dummy text ever since the 1500s, when an unknown printer took a galley of type and scrambled it to make a type specimen book.<br><br>It has survived not only five centuries, but also the leap into electronic typesetting, remaining essentially unchanged.</p>
    <div class="btn btn-white" style="left:267px;top:322px;width:172px;height:47px">Shop Now</div>
  </div>
</section>

<section class="blogs">
  <h2 class="abs center section-title" style="top:46px">Latest Blogs</h2>
  <article class="card" style="left:118px"><div class="img" role="img" aria-label="Glass cup of herbal tea with loose leaves" style="background:linear-gradient(135deg,#f3f1ec,#d9a94a 55%,#6a5a3a)"></div>
    <h4>Blogs # 01</h4><div class="meta"><span>29.8.2016</span><span>Comments ( 12 )</span><span>Share</span></div>
    <p>Lorem Ipsum is simply dummy text of the printing and typesetting industry. Lorem Ipsum has been the industry's standard dummy text ever since the 1500s.</p>
    <div class="more">READ MORE <svg width="14" height="8" viewBox="0 0 14 8"><path d="M0 4h12M9 1l3 3-3 3" fill="none" stroke="#333"/></svg></div></article>
  <article class="card" style="left:444px"><div class="img" role="img" aria-label="Cup of tea with bowls of dry tea on a wooden table" style="background:linear-gradient(135deg,#6b4226,#c48a4a 50%,#4a2c18)"></div>
    <h4>Blogs # 02</h4><div class="meta"><span>29.8.2016</span><span>Comments ( 28 )</span><span>Share</span></div>
    <p>Lorem Ipsum is simply dummy text of the printing and typesetting industry. Lorem Ipsum has been the industry's standard dummy text ever since the 1500s.</p>
    <div class="more">READ MORE <svg width="14" height="8" viewBox="0 0 14 8"><path d="M0 4h12M9 1l3 3-3 3" fill="none" stroke="#333"/></svg></div></article>
  <article class="card" style="left:770px"><div class="img" role="img" aria-label="Woman sipping tea against a green background" style="background:linear-gradient(135deg,#8fbf3a,#c8d86a 50%,#b7793e)"></div>
    <h4>Blogs # 03</h4><div class="meta"><span>29.8.2016</span><span>Comments ( 16 )</span><span>Share</span></div>
    <p>Lorem Ipsum is simply dummy text of the printing and typesetting industry. Lorem Ipsum has been the industry's standard dummy text ever since the 1500s.</p>
    <div class="more">READ MORE <svg width="14" height="8" viewBox="0 0 14 8"><path d="M0 4h12M9 1l3 3-3 3" fill="none" stroke="#333"/></svg></div></article>
  <div class="btn btn-gold" style="left:512px;top:693px;width:175px;height:48px">Browse More</div>
</section>

<section class="testimonials" role="img" aria-label="Chinese teapot and cups on a dark wooden tray">
  <h2 class="abs center section-title" style="top:38px">Testimonials</h2>
  <svg class="abs" style="left:588px;top:104px" width="26" height="22" viewBox="0 0 26 22"><path d="M0 22V12C0 5 4 1 10 0v4C7 5 5 8 5 11h5v11zM15 22V12c0-7 4-11 10-12v4c-3 1-5 4-5 7h5v11z" fill="#fff"/></svg>
  <p class="abs" style="left:330px;width:540px;top:150px;font-size:13.5px;line-height:1.45;text-align:center">Lorem Ipsum is simply dummy text of the printing and typesetting industry. Lorem Ipsum has been the industry's standard dummy text ever since the 1500s.</p>
  <p class="abs center serif" style="top:214px;font-size:24px">Daniel Ashford</p>
  <p class="abs center" style="top:250px;font-size:12px;color:#e8c24a;letter-spacing:3px">★★★★★</p>
  <svg class="abs" style="left:620px;top:270px" width="36" height="14" viewBox="0 0 36 14"><path d="M0 7h34M28 1l6 6-6 6" fill="none" stroke="#fff" stroke-width="2"/></svg>
  <div class="btn btn-white" style="left:514px;top:349px;width:172px;height:46px">View More</div>
</section>

<section class="perks">
  <div class="perk" style="left:118px">
    <svg width="30" height="30" viewBox="0 0 30 30"><path d="M15 2a9 9 0 00-9 9c0 7 9 17 9 17s9-10 9-17a9 9 0 00-9-9z" fill="none" stroke="#fff" stroke-width="2"/><circle cx="15" cy="11" r="3" fill="#fff"/></svg>
    <div><strong>Free Shipping</strong><span>Lorem Ipsum is simply dummy text.</span></div></div>
  <div class="perk" style="left:441px">
    <svg width="30" height="30" viewBox="0 0 30 30"><circle cx="15" cy="15" r="12" fill="none" stroke="#fff" stroke-width="2"/><path d="M10 15l4 4 7-8" fill="none" stroke="#fff" stroke-width="2"/></svg>
    <div><strong>Premium Support</strong><span>24/7 Customer service</span></div></div>
  <div class="perk" style="left:761px">
    <svg width="34" height="26" viewBox="0 0 34 26"><path d="M1 3h20v15H1zM21 8h7l5 5v5H21z" fill="none" stroke="#fff" stroke-width="2"/><circle cx="8" cy="21" r="3" fill="#fff"/><circle cx="27" cy="21" r="3" fill="#fff"/></svg>
    <div><strong>Payment Method</strong><span>Cash On Delivery</span></div></div>
</section>

<footer class="site-footer">
  <div class="abs col" style="left:118px;top:48px">
    <h5>Sip of Lume</h5>
    <ul class="contact">
      <li><svg width="10" height="10" viewBox="0 0 10 10"><rect x="2" y="0" width="6" height="10" rx="1" fill="#fff"/></svg>+012-345-678-9</li>
      <li><svg width="10" height="10" viewBox="0 0 10 10"><rect x="2" y="0" width="6" height="10" rx="1" fill="#fff"/></svg>+012-345-678-9</li>
      <li><svg width="10" height="10" viewBox="0 0 10 10"><path d="M0 2h10v7H0z M0 2l5 4 5-4" fill="none" stroke="#fff"/></svg>info@sipoflume.com</li>
      <li><svg width="10" height="10" viewBox="0 0 10 10"><path d="M5 0a4 4 0 00-4 4c0 3 4 6 4 6s4-3 4-6a4 4 0 00-4-4z" fill="#fff"/></svg>14 Amber Lane</li>
      <li style="padding-left:20px">Northbrook, NY 10010</li>
    </ul>
  </div>
  <div class="abs col" style="left:418px;top:48px">
    <h5>Quick Link</h5>
    <ul><li>› Home</li><li>› About</li><li>› Leaf tea</li><li>› Blogs</li><li>› Contact</li></ul>
  </div>
  <div class="abs col" style="left:645px;top:48px">
    <h5>Accounts</h5>
    <ul><li>Login</li><li>Register</li><li>My Account</li><li>Checkout</li><li>My Wishlist</li></ul>
  </div>
  <div class="abs col" style="left:843px;top:48px;width:235px">
    <h5>Newsletter</h5>
    <p style="font-size:12.5px;line-height:1.4">Lorem Ipsum is simply dummy text of the printing and typesetting industry.</p>
    <div style="margin-top:14px;width:230px;height:28px;background:#fff;color:#888;font-size:11px;padding:7px 8px">Email Address</div>
    <div style="margin-top:10px;width:96px;height:26px;background:var(--gold-deep);font-size:11px;font-weight:600;display:flex;align-items:center;justify-content:center">SUBSCRIBE</div>
  </div>
</footer>

<section class="copyright">
  <p class="abs" style="left:118px;top:24px;font-size:12px">Copyright © 2018 SIP OF LUME . All Right Reserve</p>
  <div class="abs cards"><span></span><span></span><span></span><span></span><span></span><span></span></div>
</section>

</body>
</html>
```